Emerging Ed-Tech Startup seeking Stationery Designs!

We are in need of basic set of stationery designs to be used for our business operations, letters, emails, and in-office materials. We are a technology startup enhancing on campus work experience offerings by establishing a collaborative work environment for the completion of such tasks.

Our colors are Vibrant Tiffany Blue/Black/White.

Website: www.campusnorthway.com (Still under construction aside from the landing pages)

Please make sure the designs use a brighter more vibrant tiffany blue color than seen in the image files uploaded. We are not using those materials.

Our logo has been added as a file as well, please use that for any designs (include that logo). Thank you.

```html
<!DOCTYPE html>
<html lang="en">
<head>
<meta charset="utf-8">
<title>Campus Northway Stationery</title>
<link rel="stylesheet" href="https://fonts.googleapis.com/css2?family=Josefin+Sans:wght@400;600;700&family=Arimo&family=PT+Sans&display=swap">
<style>
  :root {
    --tiffany: #12e6ea;
    --ink: #111111;
    --paper: #ffffff;
    --backdrop: #a98a63;
    --muted: #3a3a3a;
    --ghost: #e6eef0;
    --shadow: 0 2px 5px rgba(0,0,0,.45);
  }
  * { box-sizing: border-box; margin: 0; padding: 0; }
  html, body { width: 1200px; height: 694px; overflow: hidden; }
  body { background: var(--backdrop); font-family: "Josefin Sans", sans-serif; color: var(--ink); }
  .canvas { position: relative; width: 1200px; height: 694px; }
  .sheet { position: absolute; background: var(--paper); box-shadow: var(--shadow); overflow: hidden; }

  .brand { position: absolute; display: flex; align-items: center; gap: 4px;
           font-family: "Josefin Sans", sans-serif; font-weight: 700; color: var(--ink);
           line-height: 1; letter-spacing: .3px; text-transform: uppercase; }
  .brand-mark { width: 9px; height: 9px; background: var(--tiffany); flex: none; }
  .brand-name { display: flex; flex-direction: column; gap: 2px; }

  .small { font-size: 7px; color: var(--muted); letter-spacing: .2px; display: flex; align-items: center; gap: 3px; white-space: nowrap; }
  .small svg { width: 7px; height: 7px; fill: var(--ink); flex: none; }
  .rule-accent { position: absolute; left: 0; right: 0; height: 3px; background: var(--tiffany); }
  .footer-row { position: absolute; left: 0; right: 0; display: flex; justify-content: center; gap: 6px; }

  /* letterhead */
  .letterhead { left: 35px; top: 39px; width: 346px; height: 447px; }
  .letterhead .brand { left: 17px; top: 15px; font-size: 14px; }
  .side-address { position: absolute; border-left: 1px solid #999; padding-left: 3px; }
  .letterhead .side-address { right: 10px; top: 30px; }
  .ghost-name { position: absolute; font-weight: 700; color: var(--ghost); line-height: .9; text-transform: uppercase; }
  .letterhead .ghost-name { left: 95px; top: 160px; font-size: 40px; }

  /* fax */
  .fax { left: 420px; top: 39px; width: 345px; height: 447px; }
  .fax .brand { left: 25px; top: 15px; font-size: 14px; }
  .fax .side-address { left: 244px; top: 18px; display: flex; flex-direction: column; gap: 5px; }
  .fax .side-address .small { letter-spacing: 0; }
  .fax-title { position: absolute; left: 25px; top: 96px; font-family: "Arimo", sans-serif; font-size: 21px; font-weight: 400; }
  .fax-fields { position: absolute; left: 28px; top: 117px; width: 288px; }
  .fax-row { position: relative; height: 40.7px; border-bottom: 1.5px solid #333;
             font-family: "Arimo", sans-serif; font-size: 8.5px; }
  .fax-row span { position: absolute; bottom: 8px; }
  .fax-row span + span { left: 187px; }

  /* envelopes */
  .envelope { left: 787px; width: 387px; height: 167px; }
  .env-plain { top: 37px; }
  .env-dark { top: 225px; }
  .env-accent { top: 408px; }
  .env-band { position: absolute; left: 0; right: 0; top: 0; height: 58px; display: flex; justify-content: center; align-items: center; }
  .env-plain .env-band { border-bottom: 1px solid #444; }
  .env-dark .env-band { background: var(--ink); }
  .env-accent .env-band { background: var(--tiffany); }
  .env-band .brand { position: static; font-size: 13px; }
  .env-dark .brand, .env-accent .brand { color: var(--paper); }
  .env-dark .brand-mark, .env-accent .brand-mark { background: var(--paper); }

  /* email signature */
  .signature { left: 30px; top: 530px; width: 367px; height: 101px; }
  .signature .brand { left: 11px; top: 11px; font-size: 11px; }
  .sig-person { position: absolute; right: 14px; top: 13px; text-align: right; text-transform: uppercase; }
  .sig-name { font-size: 9.5px; letter-spacing: .6px; }
  .sig-role { font-size: 7px; letter-spacing: .5px; margin-top: 5px; }
  .signature .rule-accent { top: 75px; }
  .signature .footer-row { top: 86px; justify-content: flex-start; padding-left: 10px; gap: 5px; }
  .signature .small { letter-spacing: 0; }
  .caption { position: absolute; left: 141px; top: 647px; color: var(--paper); font-family: "PT Sans", sans-serif; font-size: 18px; }

  /* compliment slip */
  .slip { left: 458px; top: 511px; width: 387px; height: 169px; }
  .slip .brand { left: 15px; top: 14px; font-size: 14px; }
  .slip .addr { position: absolute; left: 15px; top: 66px; }
  .slip .ghost-name { right: 12px; top: 92px; font-size: 12px; text-align: right; }
  .slip .rule-accent { top: 141px; }
  .slip .web { position: absolute; left: 15px; top: 151px; }
</style>
</head>
<body>
<svg width="0" height="0" style="position:absolute" aria-hidden="true">
  <symbol id="i-phone" viewBox="0 0 10 10"><path d="M2 1l2 2-1 1c1 1.5 2 2.5 3 3l1-1 2 2-1.5 1.5C4 9 1 6 .5 2.5z"/></symbol>
  <symbol id="i-mobile" viewBox="0 0 10 10"><path d="M3 0h4v10H3zM3.8 1v7h2.4V1z"/></symbol>
  <symbol id="i-globe" viewBox="0 0 10 10"><circle cx="5" cy="5" r="4.5"/></symbol>
  <symbol id="i-home" viewBox="0 0 10 10"><path d="M5 .5L.5 5H2v4.5h2.5V7h1v2.5H8V5h1.5z"/></symbol>
</svg>

<main class="canvas">
  <section class="sheet letterhead">
    <div class="brand"><span class="brand-mark"></span><span class="brand-name"><span>Campus</span><span>Northway</span></span></div>
    <div class="side-address small">House#B-14 Elm Avenue</div>
    <div class="ghost-name" aria-hidden="true">Campus<br>Northway</div>
    <div class="rule-accent" style="top:424px"></div>
    <div class="footer-row" style="top:432px">
      <span class="small"><svg><use href="#i-phone"/></svg>+91 20 4455102</span>
      <span class="small"><svg><use href="#i-mobile"/></svg>+91 14 7788320</span>
      <span class="small"><svg><use href="#i-globe"/></svg>www.campusnorthway.com</span>
    </div>
  </section>

  <section class="sheet fax">
    <div class="brand"><span class="brand-mark"></span><span class="brand-name"><span>Campus</span><span>Northway</span></span></div>
    <div class="side-address">
      <span class="small"><svg><use href="#i-phone"/></svg>+91 20 4455102</span>
      <span class="small"><svg><use href="#i-mobile"/></svg>+91 14 7788320</span>
      <span class="small"><svg><use href="#i-globe"/></svg>www.campusnorthway.com</span>
    </div>
    <h1 class="fax-title">FAX</h1>
    <div class="fax-fields">
      <div class="fax-row"><span>To</span><span>From</span></div>
      <div class="fax-row"><span>Fax</span><span>Pages</span></div>
      <div class="fax-row"><span>Phone</span><span>Date</span></div>
      <div class="fax-row"><span>Re</span><span>CC</span></div>
    </div>
    <div class="rule-accent" style="top:424px"></div>
    <div class="footer-row" style="top:432px">
      <span class="small"><svg><use href="#i-home"/></svg>House#B-14 Elm Avenue</span>
    </div>
  </section>

  <section class="sheet envelope env-plain">
    <div class="env-band"><div class="brand"><span class="brand-mark"></span><span>Campus Northway</span></div></div>
  </section>
  <section class="sheet envelope env-dark">
    <div class="env-band"><div class="brand"><span class="brand-mark"></span><span>Campus Northway</span></div></div>
  </section>
  <section class="sheet envelope env-accent">
    <div class="env-band"><div class="brand"><span class="brand-mark"></span><span>Campus Northway</span></div></div>
  </section>

  <section class="sheet signature">
    <div class="brand"><span class="brand-mark"></span><span class="brand-name"><span>Campus</span><span>Northway</span></span></div>
    <div class="sig-person">
      <div class="sig-name">Mr. Alan Reed</div>
      <div class="sig-role">Marketing Manager</div>
    </div>
    <div class="rule-accent"></div>
    <div class="footer-row">
      <span class="small"><svg><use href="#i-phone"/></svg>+91 20 4455102</span>
      <span class="small"><svg><use href="#i-mobile"/></svg>+91 14 7788320</span>
      <span class="small"><svg><use href="#i-globe"/></svg>www.campusnorthway.com</span>
      <span class="small"><svg><use href="#i-home"/></svg>House#B-14 Elm Avenue</span>
    </div>
  </section>
  <p class="caption">Email Signtaure</p>

  <section class="sheet slip">
    <div class="brand"><span class="brand-mark"></span><span class="brand-name"><span>Campus</span><span>Northway</span></span></div>
    <div class="addr small">House#B-14 Elm Avenue</div>
    <div class="ghost-name" aria-hidden="true">Campus<br>Northway</div>
    <div class="rule-accent"></div>
    <div class="web small">www.campusnorthway.com</div>
  </section>
</main>
</body>
</html>
```